FREE Network Assessment image for landing page

This graphic will be on a landing page and on the left will be Text and a download button that we change and control. The graphic for this project will be to the right.
I will add an example of the landing page area so that it makes more sense.

Please include the text from the sample - the font needs to be the same style as what we are using on the left side!

The graphic needs to be a .png file, roughly 713 x 527 white background. Use discretion on design layout.

Colors are black, Red = PMS 1795 and Gray = Cool Gray 10

Thanks,
Tom Garrick

Target Market(s)

small businesses

Industry/Entity Type

Information Technology

Font styles to use
Other font styles liked:
• See sample

Requirements
Must have
• see description
Nice to have
• Possibly small technology related image to help enhance the text but I don't want any image to compete with the text. Keep in mind the colors mentioned in the description - this is the web site colors.
Should not have
• Should not be hard to read

```html
<!DOCTYPE html>
<html lang="en">
<head>
<meta charset="utf-8">
<title>Free Network &amp; Computer Health Check Service</title>
<link rel="stylesheet" href="https://fonts.googleapis.com/css2?family=Oswald:wght@400&family=Lato:wght@400&display=swap">
<style>
  :root {
    --paper: #ffffff;
    --ink-gray: #434244;
    --red: #d3393c;
    --red-text: #c4504f;
    --button-red: #f04a4f;
    --photo-light: #d9dadc;
    --photo-dark: #5a5d63;
  }
  html, body {
    margin: 0;
    padding: 0;
    width: 1200px;
    height: 888px;
    overflow: hidden;
    background: var(--paper);
  }
  .promo {
    position: relative;
    width: 1200px;
    height: 888px;
    background: var(--paper);
    overflow: hidden;
  }
  .promo__title {
    position: absolute;
    left: 56px;
    top: 40px;
    margin: 0;
    font-family: "Oswald", "Arial Narrow", sans-serif;
    font-weight: 400;
    font-size: 76px;
    line-height: 86px;
    color: var(--ink-gray);
    letter-spacing: -0.5px;
  }
  .benefits {
    list-style: none;
    margin: 0;
    padding: 0;
  }
  .benefit {
    position: absolute;
    left: 57px;
    display: flex;
    align-items: flex-start;
  }
  .benefit__icon {
    width: 46px;
    height: 46px;
    flex: none;
    margin: 2px 6px 0 6px;
  }
  .benefit__text {
    margin-left: 22px;
    font-family: "Lato", "Helvetica Neue", sans-serif;
    font-size: 28px;
    line-height: 35px;
    color: var(--red-text);
  }
  .cta {
    position: absolute;
    left: 57px;
    top: 761px;
    width: 468px;
    height: 74px;
    border-radius: 37px;
    background: var(--button-red);
    color: var(--paper);
    font-family: "Oswald", "Arial Narrow", sans-serif;
    font-size: 33px;
    line-height: 74px;
    text-align: center;
    text-decoration: none;
  }
  .presenter-photo {
    position: absolute;
    left: 760px;
    top: 267px;
    width: 440px;
    height: 621px;
    background: linear-gradient(180deg, var(--photo-light) 0%, #a9acb1 40%, var(--photo-dark) 100%);
    border-radius: 120px 120px 0 0;
  }
</style>
</head>
<body>
<main class="promo">
  <h1 class="promo__title">FREE NETWORK &amp;<br>COMPUTER HEALTH CHECK SERVICE</h1>

  <ul class="benefits">
    <li class="benefit" style="top:279px">
      <svg class="benefit__icon" viewBox="0 0 40 40" aria-hidden="true">
        <circle cx="20" cy="20" r="19" fill="var(--red)"/>
        <path d="M11 20.5l6 6 12-13" fill="none" stroke="#fff" stroke-width="4" stroke-linecap="round" stroke-linejoin="round"/>
      </svg>
      <span class="benefit__text">Check your network’s security against hacker<br>attacks, theft, ransomware, viruses, and more.</span>
    </li>
    <li class="benefit" style="top:385px">
      <svg class="benefit__icon" viewBox="0 0 40 40" aria-hidden="true">
        <circle cx="20" cy="20" r="19" fill="var(--red)"/>
        <path d="M11 20.5l6 6 12-13" fill="none" stroke="#fff" stroke-width="4" stroke-linecap="round" stroke-linejoin="round"/>
      </svg>
      <span class="benefit__text">See who and what has access to your<br>network and data.</span>
    </li>
    <li class="benefit" style="top:490px">
      <svg class="benefit__icon" viewBox="0 0 40 40" aria-hidden="true">
        <circle cx="20" cy="20" r="19" fill="var(--red)"/>
        <path d="M11 20.5l6 6 12-13" fill="none" stroke="#fff" stroke-width="4" stroke-linecap="round" stroke-linejoin="round"/>
      </svg>
      <span class="benefit__text">Perform network and Internet speed test</span>
    </li>
    <li class="benefit" style="top:560px">
      <svg class="benefit__icon" viewBox="0 0 40 40" aria-hidden="true">
        <circle cx="20" cy="20" r="19" fill="var(--red)"/>
        <path d="M11 20.5l6 6 12-13" fill="none" stroke="#fff" stroke-width="4" stroke-linecap="round" stroke-linejoin="round"/>
      </svg>
      <span class="benefit__text">Resolve PC slowness issues, security<br>vulnerabilities and improper configurations</span>
    </li>
    <li class="benefit" style="top:667px">
      <svg class="benefit__icon" viewBox="0 0 40 40" aria-hidden="true">
        <circle cx="20" cy="20" r="19" fill="var(--red)"/>
        <path d="M11 20.5l6 6 12-13" fill="none" stroke="#fff" stroke-width="4" stroke-linecap="round" stroke-linejoin="round"/>
      </svg>
      <span class="benefit__text">Validate your backups are working and<br>recoverable in a timely fashion.</span>
    </li>
  </ul>

  <a class="cta" href="#book">BOOK AN APPOINTMENT NOW!</a>

  <div class="presenter-photo" role="img" aria-label="Photo of a smiling businessman in a grey suit giving a thumbs up and holding a laptop"></div>
</main>
</body>
</html>
```